Website design for a hair building fibre

Hi I’m needing a website made for both men and women to purchase the product is a hair building fibre that you apply to thinning hair to make your hair look really thick I’ll need the website to be easy to use professional and also very classy I will need it to work with lumen split tok fund and credit cards I’ll need to have the CEO words and everything ready so I can sell I don’t have photos that I want to put on there so I’ll need a website designer to assist me in having the beautiful photos on there I know very little about websites so I need someone to be able to do it all for me

I can only provide photos of the colours of the products
I believe there will be 8 colours to sell as well
I’ve uploaded a photo of the logo I’d really like it if the website designer can check other competitors website so my website does not look like theres, I don’t want my website to look like a copied website of the competitors I’m located in Australia.
I’m also looking for someone who can open up a Palvista and Glimmerly page and then can unload photos on them ready for consumers to view and buy.

```html
<!DOCTYPE html>
<html lang="en">
<head>
<meta charset="utf-8">
<title>Loftline Hair Building Fibre</title>
<link href="https://fonts.googleapis.com/css2?family=Montserrat:wght@300;400;500;600;700&display=swap" rel="stylesheet">
<style>
:root{
  --ink:#1c1c22;
  --text:#3a3a40;
  --accent:#6fbbe6;
  --accent-soft:#e6f1fa;
  --accent-mist:#d3e7f6;
  --white:#ffffff;
  --footer:#141417;
  --hero-a:#12303f;
  --hero-b:#2a5c6e;
}
*{margin:0;padding:0;box-sizing:border-box}
html,body{width:1200px;height:4048px;overflow:hidden}
body{font-family:'Montserrat',sans-serif;color:var(--text);background:var(--white);position:relative}
.abs{position:absolute}
.btn{position:absolute;display:flex;align-items:center;justify-content:center;border-radius:40px;font-weight:600;font-size:13px;letter-spacing:1px;text-transform:uppercase}
.btn-light{background:var(--accent);color:var(--white)}
.btn-dark{background:var(--ink);color:var(--white)}
.section-title{position:absolute;left:0;width:1200px;text-align:center;font-size:42px;font-weight:600;color:var(--ink);letter-spacing:1px}
.section-title span{color:var(--accent)}
.title-line{position:absolute;height:3px;background:var(--accent);border-radius:2px}

/* header */
.site-header{position:absolute;top:0;left:0;width:1200px;height:100px;background:var(--white);z-index:5}
.brand{position:absolute;left:40px;top:28px;color:var(--ink)}
.brand-name{font-size:30px;font-weight:300;letter-spacing:1px;line-height:1}
.brand-tag{font-size:10px;letter-spacing:3px;margin-top:4px}
.nav{position:absolute;left:430px;top:38px;display:flex;gap:38px;font-size:17px;color:var(--text)}
.nav .active{color:var(--accent);border-bottom:2px solid var(--accent);padding-bottom:4px}

/* hero */
.hero-visual{position:absolute;top:100px;left:0;width:1200px;height:860px;background:radial-gradient(circle at 30% 40%,var(--hero-b),var(--hero-a) 70%)}
.hero-product{position:absolute;left:40px;top:330px;width:300px;height:330px;border-radius:12px;background:linear-gradient(90deg,#7a1c2a,#c9c9cc 45%,#2a2a2e);opacity:.85}
.hero-model{position:absolute;left:260px;top:110px;width:340px;height:560px;border-radius:170px 170px 20px 20px;background:linear-gradient(180deg,#2c1f1c,#6b5248 60%,#d8bfae)}
.hero-copy{position:absolute;left:650px;top:250px;color:var(--white)}
.hero-copy .pre{font-size:40px;font-weight:300;letter-spacing:3px}
.hero-copy h1{font-size:92px;font-weight:300;line-height:1.05}
.hero-copy .sub{font-size:30px;font-weight:400;letter-spacing:2px}
.arrow{position:absolute;width:40px;height:40px;border-radius:50%;display:flex;align-items:center;justify-content:center}

/* about */
.about-text{position:absolute;left:110px;top:960px;width:540px;font-size:15px;line-height:1.65}
.about-blob{position:absolute;left:700px;top:900px;width:500px;height:440px;background:var(--accent-soft);border-radius:60% 0 0 55%}
.about-photo{position:absolute;left:680px;top:830px;width:360px;height:360px;border-radius:50%;background:linear-gradient(160deg,#3b5e86,#b98e74);border:10px solid var(--accent-mist)}

/* products */
.swatches{position:absolute;left:592px;top:1652px;display:flex;gap:14px}
.swatch{width:48px;height:48px;border-radius:50%;border:3px solid var(--white);box-shadow:0 0 0 1px #b8c4cc}
.product-visual{position:absolute;left:110px;top:1630px;width:390px;height:520px;border-radius:8px;background:linear-gradient(160deg,#e9e3dd,#cfc3b6 55%,#b8b4b2)}
.product-frame{position:absolute;left:80px;top:1610px;width:440px;height:560px;border-radius:10px;background:var(--accent-mist)}
.shade{position:absolute;left:596px;top:1760px}
.shade h3{font-size:36px;font-weight:600;color:var(--ink)}
.shade p.kind{font-size:20px;letter-spacing:1px;color:var(--ink);margin-top:4px}
.shade-text{position:absolute;left:596px;top:1870px;width:480px;font-size:15px;line-height:1.6;color:var(--text)}
.shade-text p+p{margin-top:10px}

/* reviews */
.avatar{position:absolute;border-radius:50%;background:linear-gradient(160deg,#d9cbc0,#8d7c72)}
.review-text{position:absolute;left:250px;top:2580px;width:700px;text-align:center;font-size:15px;line-height:1.7}
.reviewer{position:absolute;left:0;top:2726px;width:1200px;text-align:center;font-size:15px;font-weight:600;color:var(--ink)}
.reviewer span{color:#f4b400;letter-spacing:2px}
.quote{position:absolute;font-size:80px;color:#cfd6db;font-family:Georgia,serif;line-height:1}

/* gallery */
.gallery-tile{position:absolute;width:470px;height:290px;border-radius:12px;box-shadow:0 4px 16px rgba(0,0,0,.12)}

/* footer */
.footer{position:absolute;left:0;top:3660px;width:1200px;height:388px;background:var(--footer);color:#d8d8dc}
.footer .brand{left:110px;top:140px;color:var(--white)}
.footer-col{position:absolute;top:105px;font-size:15px;line-height:2}
.footer-col h4{font-size:17px;font-weight:600;color:var(--white);margin-bottom:6px}
.footer-col li{list-style:none;display:flex;align-items:center;gap:8px}
.copyright{position:absolute;left:0;top:352px;width:1200px;text-align:center;font-size:14px}
</style>
</head>
<body>

<header class="site-header">
  <div class="brand"><div class="brand-name">LOFTLINE</div><div class="brand-tag">HAIR BUILDING FIBRE</div></div>
  <nav class="nav"><span class="active">Home</span><span>Products</span><span>Shop</span><span>About</span><span>Contact</span></nav>
  <div class="btn btn-light" style="left:910px;top:30px;width:112px;height:40px">Buy Now</div>
  <svg class="abs" style="left:1050px;top:34px" width="32" height="32" viewBox="0 0 32 32"><path d="M5 10h22l-2 18H7z" fill="none" stroke="#1c1c22" stroke-width="2"/><path d="M11 10V7a5 5 0 0 1 10 0v3" fill="none" stroke="#1c1c22" stroke-width="2"/><circle cx="26" cy="8" r="6" fill="#e2574c"/></svg>
</header>

<section class="hero">
  <div class="hero-visual" role="img" aria-label="Woman with long thick dark hair on a dark teal sparkling backdrop"></div>
  <div class="hero-model" role="img" aria-label="Model with voluminous hair"></div>
  <div class="hero-product" role="img" aria-label="Three hair fibre canisters in burgundy, silver and black"></div>
  <div class="hero-copy">
    <div class="pre">WELCOME TO</div>
    <h1>LOFTLINE</h1>
    <div class="sub">HAIR BUILDING FIBRE</div>
  </div>
  <div class="btn btn-dark" style="left:650px;top:538px;width:124px;height:44px">Buy Now</div>
  <div class="arrow" style="left:30px;top:370px;background:rgba(255,255,255,.85)"><svg width="14" height="14" viewBox="0 0 14 14"><path d="M9 2 4 7l5 5" fill="none" stroke="#1c1c22" stroke-width="2"/></svg></div>
  <div class="arrow" style="left:1130px;top:370px;background:rgba(255,255,255,.85)"><svg width="14" height="14" viewBox="0 0 14 14"><path d="M5 2l5 5-5 5" fill="none" stroke="#1c1c22" stroke-width="2"/></svg></div>
  <svg class="abs" style="left:0;top:780px" width="1200" height="200" viewBox="0 0 1200 200" preserveAspectRatio="none"><path d="M0 90 C200 20 380 160 620 110 C840 60 1000 120 1200 70 V200 H0Z" fill="#fff"/></svg>
</section>

<section class="about">
  <div class="about-blob"></div>
  <h2 class="abs" style="left:110px;top:855px;font-size:42px;font-weight:600;color:var(--ink)">ABOUT <span style="color:var(--accent)">US</span></h2>
  <div class="title-line" style="left:250px;top:912px;width:70px"></div>
  <p class="about-text">Lorem ipsum dolor sit amet, consectetur adipiscing elit, sed do eiusmod tempor incididunt ut labore et dolore magna aliqua. Ut enim ad minim veniam, quis nostrud exercitation ullamco laboris nisi ut aliquip ex ea commodo consequat. Duis aute irure dolor in reprehenderit in voluptate velit esse cillum dolore eu fugiat nulla pariatur. Excepteur sint occaecat cupidatat non proident, sunt in culpa qui officia deserunt.</p>
  <div class="btn btn-light" style="left:110px;top:1222px;width:154px;height:46px">Learn More</div>
  <div class="about-photo" role="img" aria-label="Smiling man running his hand through full hair"></div>
</section>

<section class="products">
  <svg class="abs" style="left:0;top:1340px" width="1200" height="920" viewBox="0 0 1200 920" preserveAspectRatio="none"><path d="M0 60 C300 0 500 110 800 50 C1000 10 1100 40 1200 30 V860 C1000 920 700 820 400 880 C200 920 80 880 0 870Z" fill="#e6f1fa"/></svg>
  <h2 class="section-title" style="top:1480px">OUR <span>PRODUCTS</span></h2>
  <div class="title-line" style="left:540px;top:1538px;width:120px"></div>
  <div class="product-frame"></div>
  <div class="product-visual" role="img" aria-label="Woman with long platinum blonde hair beside a silver fibre canister"></div>
  <div class="swatches">
    <div class="swatch" style="background:#141414"></div>
    <div class="swatch" style="background:#3a1f22"></div>
    <div class="swatch" style="background:#6e1b24"></div>
    <div class="swatch" style="background:#8c2424"></div>
    <div class="swatch" style="background:#8a4b2c"></div>
    <div class="swatch" style="background:#a4683a"></div>
    <div class="swatch" style="background:#c39366"></div>
    <div class="swatch" style="background:#e6d6c4"></div>
  </div>
  <div class="shade"><h3>SHADE 001</h3><p class="kind">HAIR-BUILDING FIBRE</p></div>
  <div class="shade-text">
    <p>Lorem ipsum dolor sit amet, consectetur adipiscing elit, sed do eiusmod tempor incididunt ut labore et dolore</p>
    <p>Lorem ipsum dolor sit amet, consectetur adipiscing elit, sed do eiusmod tempor incididunt ut. Lorem ipsumigh dolor sit amet, consectetur adipiscing elit, sed do lorem eiusmod tempor incididunt ut labore et dolore</p>
  </div>
  <div class="btn btn-dark" style="left:596px;top:2098px;width:150px;height:48px">Buy Now</div>
</section>

<section class="reviews">
  <h2 class="section-title" style="top:2330px">OUR <span>REVIEWS</span></h2>
  <div class="title-line" style="left:540px;top:2388px;width:120px"></div>
  <div class="avatar" style="left:432px;top:2454px;width:90px;height:90px;opacity:.6" role="img" aria-label="Customer portrait"></div>
  <div class="avatar" style="left:548px;top:2446px;width:104px;height:104px;border:4px solid var(--accent)" role="img" aria-label="Featured customer portrait"></div>
  <div class="avatar" style="left:678px;top:2454px;width:90px;height:90px;opacity:.6" role="img" aria-label="Customer portrait"></div>
  <p class="review-text">Nemo enim ipsam voluptatem quia voluptas sit aspernatur aut odit aut fugit, sed quia consequuntur magni dolores eos qui ratione voluptatem sequi nesciunt. Neque porro quisquam est, qui dolorem ipsum quia dolor sit amet, consectetur, adipisci velit, sed quia non numquam eius modi tempora incidunt ut labore et dolore magnam aliquam quaerat voluptatem.</p>
  <div class="quote" style="left:290px;top:2690px">&ldquo;</div>
  <div class="quote" style="left:860px;top:2690px">&rdquo;</div>
  <div class="reviewer">Mara Quill - <span>★★★★★</span></div>
  <div class="arrow" style="left:30px;top:2610px;border:2px solid #c9d0d5"><svg width="14" height="14" viewBox="0 0 14 14"><path d="M9 2 4 7l5 5" fill="none" stroke="#9aa3a9" stroke-width="2"/></svg></div>
  <div class="arrow" style="left:1124px;top:2610px;border:2px solid var(--ink)"><svg width="14" height="14" viewBox="0 0 14 14"><path d="M5 2l5 5-5 5" fill="none" stroke="#1c1c22" stroke-width="2"/></svg></div>
</section>

<section class="gallery">
  <h2 class="section-title" style="top:2862px">GALLERY</h2>
  <div class="title-line" style="left:560px;top:2920px;width:80px"></div>
  <div class="gallery-tile" style="left:110px;top:2980px;background:linear-gradient(90deg,#b58a6a,#5a3b28 48%,#4a3020 52%,#3a2418)" role="img" aria-label="Before and after of a thinning hair parting"></div>
  <div class="gallery-tile" style="left:620px;top:2980px;background:linear-gradient(90deg,#e3c7b4,#b68a6a 48%,#c39a7c 52%,#8c6448)" role="img" aria-label="Before and after of a woman's hairline"></div>
  <div class="gallery-tile" style="left:110px;top:3310px;background:linear-gradient(90deg,#2e2a28,#6f625a 48%,#2b2523 52%,#1e1a18)" role="img" aria-label="Before and after of a man's crown"></div>
  <div class="gallery-tile" style="left:620px;top:3310px;background:linear-gradient(90deg,#9a8576,#4d3f36 48%,#3b302a 52%,#2c2420)" role="img" aria-label="Before and after of a thinning crown"></div>
</section>

<footer class="footer">
  <svg class="abs" style="left:0;top:-40px" width="1200" height="80" viewBox="0 0 1200 80" preserveAspectRatio="none"><path d="M0 50 C300 0 600 70 900 30 C1050 10 1150 30 1200 20 V80 H0Z" fill="#141417"/></svg>
  <div class="brand"><div class="brand-name">LOFTLINE</div><div class="brand-tag">HAIR BUILDING FIBRE</div></div>
  <div class="footer-col" style="left:450px"><h4>Quick Link</h4><ul><li>Home</li><li>About</li><li>Product</li><li>Reviews</li></ul></div>
  <div class="footer-col" style="left:670px"><h4>Contact</h4><ul>
    <li><svg width="14" height="14" viewBox="0 0 14 14"><path d="M3 1h3l1 3-2 1a8 8 0 0 0 4 4l1-2 3 1v3c0 1-1 2-2 2A11 11 0 0 1 1 3c0-1 1-2 2-2z" fill="#d8d8dc"/></svg>+1 555 010 2040</li>
    <li><svg width="14" height="14" viewBox="0 0 14 14"><rect x="1" y="3" width="12" height="8" fill="none" stroke="#d8d8dc" stroke-width="1.5"/><path d="M1 3l6 5 6-5" fill="none" stroke="#d8d8dc" stroke-width="1.5"/></svg>info@loftline.com</li>
    <li style="align-items:flex-start"><svg width="14" height="14" viewBox="0 0 14 14" style="margin-top:8px"><path d="M7 1a4 4 0 0 1 4 4c0 3-4 8-4 8S3 8 3 5a4 4 0 0 1 4-4z" fill="#d8d8dc"/></svg><span style="line-height:1.5;margin-top:4px">Loftline,<br>Address Comes Here</span></li>
  </ul></div>
  <div class="footer-col" style="left:960px"><h4>Get Connected</h4><ul><li>Terms&amp;conditions</li><li>Privacy Policy</li><li>Contact Us</li><li>Support</li></ul></div>
  <div class="copyright">© 2022 Loftline. All Rights Reserved</div>
</footer>

</body>
</html>
```